CREATE A BUSINESS CARD FOR A BOAT CLEANING SERVICE

WE ARE STARTING A NEW BOAT CLEANING BUSINESS. WE DIVE UNDERWATER TO CLEAN BOAT HULLS, JETTIES, UNDERWATER STRUCTURES ETC. WE ARE LOOKING FOR AN UPPERMARKET MODERN LOGO AND BUSINESS CARD AS ALOT OF OUR TARGET MARKET WILL BE HIGH END. YOU HAVE TO DESIGN A BUSINESS CARD AND LOGO SEPERATELY .
THE BUSINESS CARD DIMESNION MUST BE STANDARD SIZE.
The standard dimensions of a printed business card are 3.5 x 2 inches

Target Market(s)

UNDERWATER SERVICED

Industry/Entity Type

Business

Contact Information for Business Card

HOLLAND UNDERWATER SERVICES

Font styles to use
Serif

Colors

Designer to choose colors to be used in the design.

Requirements
Must have
• HOLLAND
Nice to have
• dark
Should not have
• more than 3 colors

```html
<!DOCTYPE html>
<html lang="en">
<head>
<meta charset="utf-8">
<title>Holland Underwater Services – Business Card</title>
<link href="https://fonts.googleapis.com/css2?family=Open+Sans:wght@400&display=swap" rel="stylesheet">
<style>
  :root {
    --page-bg: #c9d3da;
    --card-dark: #0b0c0f;
    --card-mid: #2a2b31;
    --silver: #d4d6d8;
    --aqua: #3ba3cf;
    --icon-bg: #7fc6d9;
    --text-light: #d9dbdd;
  }
  * { margin: 0; padding: 0; box-sizing: border-box; }
  html, body { width: 1200px; height: 970px; overflow: hidden; }
  body {
    background: var(--page-bg);
    font-family: "Open Sans", Arial, sans-serif;
    position: relative;
  }
  .business-card {
    position: absolute;
    left: 70px; top: 182px;
    width: 1060px; height: 606px;
    background:
      radial-gradient(ellipse 55% 70% at 22% 60%, var(--card-mid) 0%, rgba(42,43,49,0) 70%),
      linear-gradient(100deg, #1d1e23 0%, var(--card-dark) 55%, #050608 100%);
    box-shadow: 0 6px 18px rgba(0,0,0,.35);
    color: var(--text-light);
    overflow: hidden;
  }
  .brand-name {
    position: absolute;
    left: 0; right: 80px; top: 150px;
    text-align: center;
    font-size: 42px;
    font-weight: 400;
    line-height: 1;
    color: var(--silver);
  }
  .person {
    position: absolute;
    right: 626px; top: 398px;
    text-align: right;
  }
  .person-name { font-size: 40px; font-weight: 400; line-height: 1.1; color: var(--text-light); }
  .person-title { font-size: 26px; color: var(--aqua); line-height: 1.1; }
  .divider {
    position: absolute;
    left: 483px; top: 308px;
    width: 2px; height: 268px;
    background: var(--aqua);
  }
  .contact-list {
    position: absolute;
    left: 527px; top: 330px;
    list-style: none;
  }
  .contact-list li {
    display: flex; align-items: center; gap: 12px;
    font-size: 25px; height: 46px;
    color: var(--text-light);
    white-space: nowrap;
  }
  .contact-list svg { width: 20px; height: 20px; flex: none; }
</style>
</head>
<body>
  <section class="business-card">
    <p class="brand-name">Holland Underwater Services</p>

    <div class="person">
      <p class="person-name">Mara Lindqvist</p>
      <p class="person-title">Service Manager</p>
    </div>

    <div class="divider"></div>

    <ul class="contact-list">
      <li>
        <svg viewBox="0 0 20 20"><rect width="20" height="20" fill="#7fc6d9"/><rect x="4" y="6" width="12" height="8" fill="none" stroke="#0b0c0f" stroke-width="1.5"/><path d="M4 6l6 5 6-5" fill="none" stroke="#0b0c0f" stroke-width="1.5"/></svg>
        hello@hollanddive.com
      </li>
      <li>
        <svg viewBox="0 0 20 20"><rect width="20" height="20" fill="#7fc6d9"/><circle cx="10" cy="10" r="6" fill="none" stroke="#0b0c0f" stroke-width="1.5"/><path d="M4 10h12M10 4c-3 3-3 9 0 12M10 4c3 3 3 9 0 12" fill="none" stroke="#0b0c0f" stroke-width="1.2"/></svg>
        www.hollanddive.com
      </li>
      <li>
        <svg viewBox="0 0 20 20"><rect width="20" height="20" fill="#7fc6d9"/><path d="M6 4l3 3-2 2c1 2 2 3 4 4l2-2 3 3-2 2C9 16 4 11 4 6z" fill="#0b0c0f"/></svg>
        555-301-4820
      </li>
      <li>
        <svg viewBox="0 0 20 20"><rect width="20" height="20" fill="#7fc6d9"/><rect x="6" y="3" width="8" height="14" rx="1" fill="#0b0c0f"/><rect x="7.5" y="5" width="5" height="8" fill="#7fc6d9"/></svg>
        555-301-7713
      </li>
      <li>
        <svg viewBox="0 0 20 20"><rect width="20" height="20" fill="#7fc6d9"/><path d="M10 3a5 5 0 0 1 5 5c0 4-5 9-5 9s-5-5-5-9a5 5 0 0 1 5-5z" fill="#0b0c0f"/><circle cx="10" cy="8" r="2" fill="#7fc6d9"/></svg>
        1217 Harbor Row, Bayview, CA. 90512
      </li>
    </ul>
  </section>
</body>
</html>
```